Business Card Design

We are a manufacturing and distribution company with most of our customer base being supermarkets. We have established brand guidelines that are attached.

```html
<!DOCTYPE html>
<html lang="en">
<head>
<meta charset="utf-8">
<title>Corvella Business Card</title>
<link rel="stylesheet" href="https://fonts.googleapis.com/css2?family=Montserrat:wght@800&family=Arimo:wght@400;700&display=swap">
<style>
  :root {
    --backdrop: #1c1c1c;
    --brand-blue: #0a67ae;
    --brand-red: #e31b23;
    --ink: #141414;
    --paper: #ffffff;
  }
  * { margin: 0; padding: 0; box-sizing: border-box; }
  html, body { width: 1200px; height: 988px; overflow: hidden; background: var(--backdrop); }
  .canvas { position: relative; width: 1200px; height: 988px; }
  .card {
    position: absolute; left: 220px; width: 760px; height: 434px;
    border-radius: 26px; overflow: hidden;
  }
  .card-front { top: 40px; background: var(--brand-blue); }
  .card-back { top: 514px; background: var(--paper); }

  .front-brand {
    position: absolute; inset: 0;
    display: flex; flex-direction: column; align-items: center; justify-content: center; gap: 22px;
  }
  .brand-square { width: 46px; height: 46px; background: var(--paper); }
  .front-wordmark {
    font-family: "Montserrat", sans-serif; font-weight: 800; font-size: 78px;
    letter-spacing: 4px; color: var(--paper);
  }

  .back-shapes { position: absolute; inset: 0; }
  .back-wordmark {
    position: absolute; left: 52px; top: 78px;
    font-family: "Montserrat", sans-serif; font-weight: 800; font-size: 54px;
    letter-spacing: 2px; color: var(--ink);
  }
  .person { position: absolute; left: 84px; top: 160px; font-family: "Arimo", sans-serif; }
  .person-name { font-weight: 700; font-size: 30px; letter-spacing: 1px; }
  .person-name .first { color: var(--brand-red); }
  .person-name .last { color: var(--brand-blue); }
  .person-role { font-size: 16px; color: var(--ink); margin-top: 2px; }

  .contact {
    position: absolute; left: 150px; top: 290px;
    font-family: "Arimo", sans-serif; font-size: 16px; line-height: 22px; color: var(--paper);
    list-style: none;
  }
  .contact .address { margin-bottom: 8px; }
  .contact li { display: flex; align-items: center; gap: 8px; }
  .contact svg { width: 14px; height: 14px; flex: none; }
</style>
</head>
<body>
<main class="canvas">
  <section class="card card-front">
    <div class="front-brand">
      <div class="brand-square"></div>
      <div class="front-wordmark">CORVELLA</div>
    </div>
  </section>

  <section class="card card-back">
    <svg class="back-shapes" viewBox="0 0 760 434" width="760" height="434">
      <polygon points="0,262 640,170 560,434 0,434" fill="var(--brand-blue)"/>
      <polygon points="640,170 700,0 760,0 760,434 560,434" fill="var(--brand-red)"/>
      <rect x="575" y="170" width="100" height="100" fill="var(--paper)"/>
    </svg>

    <div class="back-wordmark">CORVELLA</div>

    <div class="person">
      <div class="person-name"><span class="first">DALEN</span> <span class="last">MARSH</span></div>
      <div class="person-role">CEO/Founder</div>
    </div>

    <ul class="contact">
      <li class="address">2190 Harlow Lane<br>Country Name, AB 40312</li>
      <li>
        <svg viewBox="0 0 16 16"><path d="M3 1h3l1.5 4-2 1.3a9 9 0 0 0 4.2 4.2L11 8.5l4 1.5v3a2 2 0 0 1-2 2A12 12 0 0 1 1 3a2 2 0 0 1 2-2z" fill="var(--paper)"/></svg>
        555-014-2387
      </li>
      <li>
        <svg viewBox="0 0 16 16"><rect x="1" y="3" width="14" height="10" fill="var(--paper)"/><path d="M1 3l7 6 7-6" stroke="var(--brand-blue)" stroke-width="1.5" fill="none"/></svg>
        hello@corvella.com.au
      </li>
      <li>
        <svg viewBox="0 0 16 16"><circle cx="8" cy="8" r="7" fill="var(--paper)"/><path d="M1 8h14M8 1c3 3 3 11 0 14M8 1c-3 3-3 11 0 14" stroke="var(--brand-blue)" stroke-width="1.2" fill="none"/></svg>
        www.corvella.com.au
      </li>
    </ul>
  </section>
</main>
</body>
</html>
```